KRV Business Card

Looking for a business card for my restaurant group I own. Four different concepts:

Copperfield Alehouse
Bristow Alehouse
Tanager's Stone Hearth Kitchen
Pellston Patty Company

Card doesn't need to include all the logos.

```html
<!DOCTYPE html>
<html lang="en">
<head>
<meta charset="utf-8">
<title>KRV Business Card</title>
<link href="https://fonts.googleapis.com/css2?family=Open+Sans:wght@400;600;700&display=swap" rel="stylesheet">
<style>
  :root {
    --backdrop: #2b2d30;
    --card: #151516;
    --gold: #d4b36a;
    --white: #f2f2f2;
    --grey: #8e8f93;
  }
  * { margin: 0; padding: 0; box-sizing: border-box; }
  html, body { width: 1200px; height: 900px; overflow: hidden; }
  body {
    background: var(--backdrop);
    font-family: "Open Sans", sans-serif;
    position: relative;
  }
  .card {
    position: absolute;
    width: 560px;
    height: 320px;
    background: var(--card);
    box-shadow: 0 14px 30px rgba(0,0,0,0.45);
    overflow: hidden;
  }
  .card--front { left: 120px; top: 100px; }
  .card--back { left: 520px; top: 480px; }

  .brand {
    display: flex;
    align-items: center;
    gap: 12px;
    color: var(--gold);
    font-weight: 600;
    text-transform: uppercase;
    letter-spacing: 0.14em;
    white-space: nowrap;
  }
  .brand__mark {
    width: 14px; height: 14px;
    background: var(--gold);
    flex: none;
  }
  .card--front .brand {
    position: absolute;
    left: 0; right: 0; top: 0; bottom: 0;
    justify-content: center;
    font-size: 24px;
  }
  .card--back .brand {
    position: absolute;
    right: 40px; top: 62px;
    font-size: 17px;
  }
  .card--back .brand__mark { width: 11px; height: 11px; }

  .divider {
    position: absolute;
    left: 56px; right: 40px; top: 176px;
    height: 1px;
    background: var(--gold);
  }
  .person {
    position: absolute;
    left: 56px; top: 118px;
  }
  .person__name {
    color: var(--gold);
    font-weight: 700;
    font-size: 20px;
    line-height: 1.1;
  }
  .person__role {
    color: var(--white);
    font-size: 14px;
    margin-top: 4px;
  }
  .contacts {
    position: absolute;
    left: 56px; top: 190px;
    list-style: none;
  }
  .contacts li {
    display: flex;
    align-items: center;
    gap: 12px;
    color: var(--white);
    font-size: 13.5px;
    line-height: 24px;
  }
  .contacts svg { width: 12px; height: 12px; flex: none; }
  .company-line {
    position: absolute;
    right: 40px; bottom: 34px;
    color: var(--white);
    font-size: 13px;
  }
  .gold-band {
    position: absolute;
    left: 0; right: 0; bottom: 0;
    height: 10px;
    background: var(--gold);
  }
</style>
</head>
<body>

  <section class="card card--front">
    <div class="brand"><span class="brand__mark"></span>Kestrel Ridge Ventures</div>
  </section>

  <section class="card card--back">
    <div class="brand"><span class="brand__mark"></span>Kestrel Ridge Ventures</div>

    <div class="person">
      <p class="person__name">Daniel Orsund</p>
      <p class="person__role">Project Manager</p>
    </div>

    <div class="divider"></div>

    <ul class="contacts">
      <li>
        <svg viewBox="0 0 24 24" aria-hidden="true"><path fill="#d4b36a" d="M6.6 10.8a15 15 0 0 0 6.6 6.6l2.2-2.2a1 1 0 0 1 1-.25 11.4 11.4 0 0 0 3.6.57 1 1 0 0 1 1 1V20a1 1 0 0 1-1 1A17 17 0 0 1 3 4a1 1 0 0 1 1-1h3.5a1 1 0 0 1 1 1c0 1.25.2 2.45.57 3.57a1 1 0 0 1-.25 1z"/></svg>
        555-014-2290
      </li>
      <li>
        <svg viewBox="0 0 24 24" aria-hidden="true"><rect x="2" y="5" width="20" height="14" rx="1.5" fill="#d4b36a"/><path d="M3 6l9 7 9-7" fill="none" stroke="#151516" stroke-width="2"/></svg>
        dan@krvrestaurants.com
      </li>
      <li>
        <svg viewBox="0 0 24 24" aria-hidden="true"><circle cx="12" cy="12" r="10" fill="#d4b36a"/><path d="M2 12h20M12 2c3 3 3 17 0 20M12 2c-3 3-3 17 0 20" fill="none" stroke="#151516" stroke-width="1.5"/></svg>
        www.krvrestaurants.com
      </li>
    </ul>

    <p class="company-line">Kestrel Ridge Ventures</p>
    <div class="gold-band"></div>
  </section>

</body>
</html>
```